Norvane Freight and Provision Service Brochure

Please see http://www.norvanefreight.example for who we are and what we do.
We would like to see a design that matches the industry we work in i.e. Oil and Gas. The design should communicate large, heavy field operations, supply of vast bulk fuel quantities to our US and Afghan Military customers, plus financial independence and the companies whatever it takes attitude operation in remote often hostile areas. Dark colors like on the website - contrasting our green logo. A strong focus on our past performance/past experience.

Target Market(s)

Military Customers, Partners, Subcontractors

Industry/Entity Type

Industry

Contact Information for Business Card

Display of Address, Phone, email etc. of our 4 offices

Font styles to use
Sans Serif

Requirements
Must have
• Glossy brochure, modern, cool design. Great display (map) of our offices in the Middle East, Europe and Central Asia. A focus on our past performance/past experience. Customer logos/references
Nice to have
• Prominent highlighted watermark logo
Should not have
• Standard A4/Letter brochure

```html
<!DOCTYPE html>
<html lang="en">
<head>
<meta charset="utf-8">
<title>Norvane Freight and Provision – About Spread</title>
<link rel="stylesheet" href="https://fonts.googleapis.com/css2?family=Barlow:wght@400;600&family=Arimo&display=swap">
<style>
  :root {
    --canvas: #ffffff;
    --navy: #0d1f5c;
    --green: #7fd400;
    --body-text: #4a4f57;
    --label: #111111;
    --sky-top: #2f76b8;
    --sky-mid: #7ba7b8;
    --sky-glow: #e49a45;
    --horizon: #c5652a;
    --plant: #1c1a1d;
    --water: #221b10;
  }
  * { margin: 0; padding: 0; box-sizing: border-box; }
  html, body { width: 1200px; height: 1000px; overflow: hidden; background: var(--canvas); }
  body { position: relative; font-family: "Barlow", Arial, sans-serif; }

  .spread { position: absolute; left: 0; top: 288px; width: 1200px; height: 424px; overflow: hidden; }

  .refinery-photo {
    position: absolute; inset: 0;
    background:
      linear-gradient(180deg, transparent 0%, transparent 72%, rgba(167,122,31,.55) 80%, var(--water) 100%),
      linear-gradient(180deg, transparent 0%, transparent 62%, var(--plant) 63%, var(--plant) 79%, transparent 80%),
      linear-gradient(180deg, var(--sky-top) 0%, var(--sky-mid) 28%, var(--sky-glow) 50%, var(--horizon) 62%);
  }

  .page-right {
    position: absolute; left: 877px; top: 0; width: 323px; height: 424px;
    background: rgba(255,255,255,0.92);
  }

  .section-band {
    position: absolute; left: 600px; top: 67px; width: 277px; height: 56px;
    background: var(--navy);
    display: flex; align-items: center; padding-left: 40px;
  }
  .section-band h1 {
    color: #fff; font-size: 14px; font-weight: 600; letter-spacing: .5px;
  }

  .brand {
    position: absolute; left: 50px; top: 78px;
    display: flex; align-items: center; gap: 6px;
  }
  .brand-dot { width: 14px; height: 14px; border-radius: 50%; background: var(--green); }
  .brand-name { color: var(--green); font-size: 13px; font-weight: 600; }

  .about-copy {
    position: absolute; left: 51px; top: 134px; width: 230px;
    font-size: 7.6px; line-height: 9.6px; letter-spacing: .3px; color: var(--body-text);
  }
  .about-copy p + p { margin-top: 6px; }

  .folio {
    position: absolute; left: 263px; top: 395px; width: 19px; height: 28px;
    background: var(--green); color: #fff; font-size: 6px;
    display: flex; align-items: center; justify-content: center;
  }

  .page-label {
    position: absolute; top: 750px; font-family: "Arimo", Arial, sans-serif;
    font-size: 24px; color: var(--label);
  }
  .page-label.left { left: 323px; }
  .page-label.right { left: 855px; }
</style>
</head>
<body>
  <section class="spread">
    <div class="refinery-photo" role="img" aria-label="Oil refinery lit up at dusk beside a river, golden lights reflected on the water under a blue and orange sky"></div>

    <div class="section-band"><h1>ABOUT NORVANE</h1></div>

    <div class="page-right">
      <div class="brand">
        <span class="brand-name">Norvane</span>
        <span class="brand-dot"></span>
      </div>
      <div class="about-copy">
        <p>Norvane is an established, reliable specialist in the provision of petroleum products, oils and lubricants and related fuel management, logistics and financial services, in support of our customers' operations in Central Asia and the Central/Eastern Europe (CEE) area. From the source to solution, we provide total end-to-end fuel supply and logistics solutions to defence forces and commercial sector clients efficiently and economically all over Central Asia and the CEE region.</p>
        <p>We respond to the needs of customers by utilizing innovative technology and a variety of equipment to provide you with superior, comprehensive logistics and fuel supply services. Our ability to deliver operational excellence for government and commercial endeavours in high-risk conditions is based on our expertise, reliable supply, focus on quality, full spectrum of services and overall value.</p>
        <p>Our proven performance track record of delivering procurement, transportation, storage, technology and distribution services to clients working in Central Asia and the CEE region is unmatched. Our proven history of delivering the highest quality of products and services rapidly and securely in all conditions sets is second to None in our industry. The trust and confidence based on our strength of performance given to us by our customers has been and is reflected in being awarded with many Prime-Vendor Contracts from the Allied Field Support Command, the Ministry of Supply of Castarra, the Office of Regional Provision of Veldora, just to name a few of them.</p>
      </div>
      <div class="folio">3</div>
    </div>
  </section>

  <div class="page-label left">Page 2</div>
  <div class="page-label right">Page 3</div>
</body>
</html>
```